Modern HomePage Design for Church

We are looking for a modern homepage design using the sections we put together in the template. The colors we want are blue, black, grey, and white. We do not want use the colors in the logo. Please modify the logo color to match the website color scheme.

Target Market(s)

Church

Industry/Entity Type

Church

Number of Pages Required

1 page

Colors
0293ce
ffffff
474747
9d9d9d

```html
<!DOCTYPE html>
<html lang="en">
<head>
<meta charset="utf-8">
<title>Wellspring Grace Church — Home</title>
<link rel="stylesheet" href="https://fonts.googleapis.com/css2?family=Montserrat:wght@400;500;600;700&family=Open+Sans:wght@400;600&display=swap">
<style>
:root{
  --blue:#0293ce;
  --navy:#1a4a9a;
  --deep:#0f3b85;
  --ink:#222222;
  --dark:#474747;
  --grey:#9d9d9d;
  --light:#ececec;
  --white:#ffffff;
  --footer:#2b2b2b;
}
*{margin:0;padding:0;box-sizing:border-box}
html,body{width:1200px;height:4245px;overflow:hidden;background:var(--white)}
body{position:relative;font-family:"Open Sans",sans-serif;color:var(--dark);font-size:13px;line-height:1.6}
.abs{position:absolute}
h1,h2,h3,h4{font-family:"Montserrat",sans-serif;font-weight:500}
.btn{display:inline-block;font-family:"Montserrat",sans-serif;font-size:12px;font-weight:600;text-transform:uppercase;letter-spacing:.5px;padding:9px 20px}
.btn-white{background:var(--white);color:var(--ink)}
.btn-ghost{border:1px solid #cfcfcf;color:var(--grey);font-size:11px;padding:7px 16px;font-weight:500}
.btn-navy{background:var(--navy);color:var(--white);text-transform:none;font-size:14px;padding:10px 22px}
.btn-dark{background:var(--dark);color:var(--white);padding:7px 14px;font-size:12px}

/* hero */
.hero{left:0;top:0;width:1200px;height:617px;background:linear-gradient(180deg,#3a2a1f 0%,#6b4a30 35%,#8a6848 55%,#4a3322 80%,#2a1d14 100%)}
.topnav{left:0;top:0;width:1200px;height:38px;background:rgba(0,0,0,.35)}
.logo-box{left:145px;top:0;width:210px;height:116px;background:var(--white);display:flex;flex-direction:column;align-items:center;justify-content:center;gap:8px}
.logo-box .mark{width:22px;height:22px;background:var(--navy);border-radius:50%}
.logo-box .name{font-family:"Montserrat",sans-serif;font-weight:700;color:var(--navy);font-size:20px;line-height:1.05;text-align:center;text-transform:uppercase}
.menu{left:462px;top:12px;width:470px;display:flex;justify-content:space-between;font-family:"Montserrat",sans-serif;font-size:10px;line-height:14px;color:var(--white);text-transform:uppercase;letter-spacing:.3px}
.menu .active{font-weight:700}
.donate-top{left:960px;top:0;width:95px;height:38px;background:var(--ink);color:var(--white);font-family:"Montserrat",sans-serif;font-size:11px;font-weight:600;display:flex;align-items:center;justify-content:center}
.worship{left:865px;top:68px;color:var(--white);font-family:"Montserrat",sans-serif;font-size:12px;display:flex;align-items:center;gap:6px;text-transform:uppercase}
.hero-title{left:360px;top:250px;width:480px;text-align:center;color:var(--white);font-size:24px;font-weight:600;line-height:1.3;text-transform:uppercase}
.hero-btn{left:540px;top:355px}
.arrow{top:312px}

.visitor{left:0;top:617px;width:1200px;height:50px;background:var(--light);display:flex;align-items:center;justify-content:center;gap:18px;font-size:14px;color:var(--dark)}

/* welcome */
.welcome-title{left:145px;top:735px;width:580px;white-space:nowrap;color:var(--navy);font-size:28px;line-height:1.2}
.welcome-text{left:145px;top:790px;width:565px;font-size:11px;color:#666}
.welcome-text p{margin-bottom:14px}
.welcome-photo{left:738px;top:742px;width:312px;height:243px;background:linear-gradient(120deg,#d8d8d8,#b7b7b7 50%,#8c1e22 80%,#c9c9c9);box-shadow:4px 4px 8px rgba(0,0,0,.25)}

/* countdown */
.countdown{left:0;top:1070px;width:1200px;height:360px;background:linear-gradient(180deg,#2b5cb0,#1d4797 60%,#173d86)}
.timer{left:432px;top:1150px;display:flex;gap:12px}
.timer .unit{width:75px;height:75px;border-radius:50%;border:2px solid rgba(255,255,255,.45);color:var(--white);display:flex;flex-direction:column;align-items:center;justify-content:center}
.timer b{font-family:"Montserrat",sans-serif;font-size:30px;font-weight:600;line-height:1}
.timer small{font-size:8px;text-transform:uppercase}
.event-name{left:300px;top:1247px;width:600px;text-align:center;color:var(--white);font-size:21px;font-weight:600}
.event-date{left:300px;top:1278px;width:600px;text-align:center;color:var(--white);font-size:13px}
.count-btn{left:540px;top:1310px}

/* features */
.feature{top:1505px;width:300px;text-align:center}
.feature h3{color:var(--navy);font-size:22px;margin:10px 0 6px}
.feature p{font-size:10px;color:#555;line-height:1.5;margin-bottom:12px}
.feature svg{display:block;margin:0 auto}

/* grid */
.tile{width:300px;height:300px}
.involved{left:300px;top:2110px;width:600px;height:300px;background:#2e2e2e;color:var(--white);text-align:center;padding-top:75px}
.involved h2{font-size:30px;font-weight:400;margin-bottom:14px}
.involved p{font-size:10px;line-height:1.5;margin:0 auto 12px;width:300px}
.involved .btn-ghost{color:var(--white);border-color:#888}

/* story */
.story{left:0;top:2410px;width:600px;height:355px;background:#e9e9e9}
.story-title{left:145px;top:2458px;width:430px;color:var(--navy);font-size:14px;line-height:1.5}
.story-date{left:145px;top:2525px;font-size:12px;color:var(--dark)}
.story-text{left:145px;top:2555px;width:410px;font-size:10px;color:#666;line-height:1.55}
.story-btn{left:145px;top:2685px}
.story-photo{left:600px;top:2410px;width:600px;height:355px;background:linear-gradient(180deg,#1e3c7a,#2d57a1 40%,#c87a3c 70%,#3a2418)}

/* pastor & podcasts */
.sec-title{color:var(--navy);font-size:28px;font-weight:600}
.pastor-photo{left:145px;top:2885px;width:180px;height:215px;background:linear-gradient(180deg,#ededed,#bdbdbd 50%,#1c1c1c)}
.pastor-text{left:332px;top:2880px;width:265px;font-size:10px;color:#666;line-height:1.55}
.pod{left:628px;width:430px;display:flex;gap:14px;align-items:center;padding-bottom:14px;border-bottom:1px solid #ddd}
.pod .play{width:38px;height:38px;border-radius:50%;background:var(--ink);flex:none;display:flex;align-items:center;justify-content:center}
.pod h4{font-size:14px;color:var(--ink);line-height:1.3}
.pod span{font-size:10px;color:var(--grey)}

/* events */
.events{left:0;top:3100px;width:1200px;height:828px;background:#ececec}
.events-title{left:0;top:3168px;width:1200px;text-align:center;font-size:32px}
.card{left:145px;width:910px;height:192px;background:var(--white);display:flex}
.card .ph{width:320px;height:192px;flex:none}
.card .body{padding:28px 30px}
.card h4{font-size:18px;color:var(--ink);margin-bottom:6px}
.card .when{font-size:12px;color:var(--dark);margin-bottom:14px}
.card p{font-size:10px;color:#666;line-height:1.55}
.card .more{font-size:10px;color:var(--navy);font-weight:600;text-transform:uppercase}

/* footer */
.footer{left:0;top:3928px;width:1200px;height:317px;background:var(--footer);color:#ccc}
.fcol h4{color:var(--white);font-size:19px;margin-bottom:18px}
.fitem{display:flex;gap:12px;margin-bottom:16px}
.fitem .th{width:65px;height:45px;flex:none}
.fitem p{font-size:10px;line-height:1.45;color:#bbb}
.tags{display:flex;flex-wrap:wrap;gap:8px;width:300px}
.tags span{border:1px solid #666;font-size:11px;padding:3px 10px;color:#ddd}
.flinks{left:145px;top:4180px;display:flex;gap:10px;font-size:10px;color:#bbb}
.copy{left:145px;top:4203px;font-size:10px;color:#999}
.social{left:965px;top:4188px;display:flex;gap:14px}
.social i{width:14px;height:14px;border-radius:50%;background:#888;display:block}
</style>
</head>
<body>

<!-- hero -->
<div class="abs hero" role="img" aria-label="Church interior with wooden pews and arched windows"></div>
<div class="abs topnav"></div>
<div class="abs logo-box"><span class="mark"></span><span class="name">Wellspring<br>Grace Church</span></div>
<nav class="abs menu"><span class="active">Home</span><span>Team</span><span>Features</span><span>Events</span><span>Sermons</span><span>Blog</span><span>Contacts</span></nav>
<div class="abs donate-top">Donate Now</div>
<div class="abs worship"><svg width="11" height="11" viewBox="0 0 12 12"><circle cx="6" cy="6" r="5.5" fill="#fff"/><path d="M6 3v3.3l2 1.2" stroke="#333" stroke-width="1.3" fill="none"/></svg>Sunday Worship : 10:15 AM</div>
<h1 class="abs hero-title">Etiam mattis augue vehicula odio posuere amet tempus lectus luctus</h1>
<a class="abs btn btn-white hero-btn">Read More</a>
<svg class="abs arrow" style="left:55px" width="20" height="30" viewBox="0 0 20 30"><path d="M15 3 4 15l11 12" stroke="#fff" stroke-width="4" fill="none"/></svg>
<svg class="abs arrow" style="left:1125px" width="20" height="30" viewBox="0 0 20 30"><path d="m5 3 11 12L5 27" stroke="#fff" stroke-width="4" fill="none"/></svg>

<div class="abs visitor">First Time Visitor?.... Find out how, where and when we worship. We hope to see you soon! <span class="btn btn-dark">Visitors Info</span></div>

<!-- welcome -->
<h2 class="abs welcome-title">Welcome to Wellspring Grace Church</h2>
<div class="abs welcome-text">
<p>Mauris bibendum fringilla velit, nulla in lorem at massa pellentesque posuere. Nulla tristique posuere molestie. Aliquam erat volutpat. Etiam quis aliquet risus. Duis ornare erat eget magna dapibus, in accumsan quam pharetra. Nam tempus, quam in bibendum vulputate, sapien dolor viverra nisi vitae euismod elit turpis et nulla.</p>
<p>Aliquam erat volutpat. Pellentesque blandit lacus eget nunc faucibus, at tincidunt eros viverra. Phasellus consequat sagittis nisl suscipit feugiat. Cras eget leo sed nunc hendrerit ultricies eu ut nisl. Praesent iaculis faucibus urna sit amet lacinia. Maecenas consequat justo enim, ac mattis massa imperdiet quis. Fusce eget neque elit. Sed augue orci, elementum in magna congue, tincidunt vulputate erat. Aliquam consectetur orci molestie dictum molestie. Proin eget congue nulla, vel tempor diam.</p>
</div>
<div class="abs welcome-photo" role="img" aria-label="Pastor and a woman holding a book"></div>

<!-- countdown -->
<div class="abs countdown" role="img" aria-label="Congregation seen from above, tinted blue"></div>
<div class="abs timer">
  <div class="unit"><b>08</b><small>Days</small></div>
  <div class="unit"><b>15</b><small>Hours</small></div>
  <div class="unit"><b>28</b><small>Minutes</small></div>
  <div class="unit"><b>53</b><small>Seconds</small></div>
</div>
<h3 class="abs event-name">Curabitur venenatis lacinia</h3>
<div class="abs event-date">April 7, 2019 &nbsp;at &nbsp;10:15 AM</div>
<a class="abs btn btn-white count-btn">Read More</a>

<!-- features -->
<div class="abs feature" style="left:135px">
  <svg width="80" height="70" viewBox="0 0 80 70" fill="none" stroke="#1a4a9a" stroke-width="2.5" stroke-linejoin="round"><path d="M6 28 22 12l14 6 10-4 10 4 18 16-26 26-20-20"/><path d="M22 12 40 30"/><path d="M30 42l8 8M24 48l8 8"/></svg>
  <h3>What We Belive</h3>
  <p>Aenean facilisis tincidunt lectus, id dictum nisi luctus eget. Vivamus efficitur ex condimentum, malesuada eros eget, feugiat nibh mattis augue.</p>
  <span class="btn btn-ghost">Read More</span>
</div>
<div class="abs feature" style="left:450px">
  <svg width="80" height="70" viewBox="0 0 80 70" fill="none" stroke="#1a4a9a" stroke-width="2.5"><circle cx="40" cy="36" r="28"/><path d="M40 18v18l12 8"/><path d="M34 4h12"/></svg>
  <h3>Services &amp; Locations</h3>
  <p>Aenean facilisis tincidunt lectus, id dictum nisi luctus eget. Vivamus efficitur ex condimentum, malesuada eros eget, feugiat nibh mattis augue.</p>
  <span class="btn btn-ghost">Read More</span>
</div>
<div class="abs feature" style="left:765px">
  <svg width="80" height="70" viewBox="0 0 80 70" fill="none" stroke="#1a4a9a" stroke-width="2.5"><circle cx="44" cy="20" r="16"/><path d="M44 10v20M49 14h-7a3 3 0 0 0 0 6h4a3 3 0 0 1 0 6h-7"/><path d="M8 56h14l14 6 26-12-4-4-20 6H30"/></svg>
  <h3>Donate Now</h3>
  <p>Aenean facilisis tincidunt lectus, id dictum nisi luctus eget. Vivamus efficitur ex condimentum, malesuada eros eget, feugiat nibh mattis augue.</p>
  <span class="btn btn-ghost">Read More</span>
</div>

<!-- photo grid -->
<div class="abs tile" style="left:0;top:1810px;background:linear-gradient(135deg,#2a1a10,#7a4a2a,#1e120a)" role="img" aria-label="Hands folded in prayer"></div>
<div class="abs tile" style="left:300px;top:1810px;background:linear-gradient(160deg,#3a2a20,#d8c8b8 50%,#2a1a12)" role="img" aria-label="Choir singing"></div>
<div class="abs tile" style="left:600px;top:1810px;background:linear-gradient(135deg,#101010,#5a4030 55%,#222)" role="img" aria-label="Man reading a bible"></div>
<div class="abs tile" style="left:900px;top:1810px;background:linear-gradient(180deg,#9cc37a,#4d7a3a 50%,#151515)" role="img" aria-label="Raised hands at a worship service"></div>
<div class="abs tile" style="left:0;top:2110px;background:linear-gradient(135deg,#f3d36a,#c8652d 40%,#3a5fa0 70%,#2a1a20)" role="img" aria-label="Stained glass window"></div>
<div class="abs involved">
  <h2>Get Involved</h2>
  <p>Aenean facilisis tincidunt lectus, id dictum nisi luctus eget. Vivamus efficitur ex condimentum, malesuada eros eget, feugiat nibh mattis augue.</p>
  <span class="btn btn-ghost">Read More</span>
</div>
<div class="abs tile" style="left:900px;top:2110px;background:linear-gradient(180deg,#6a5040,#a78068 50%,#3a2820)" role="img" aria-label="Congregation seated in a church"></div>

<!-- story -->
<div class="abs story"></div>
<h3 class="abs story-title">Maecenas vel tortor accumsan quam varius imperdiet vel eget elit. Aenean facilisis tincidunt lectus.</h3>
<div class="abs story-date">5 April, 2019</div>
<div class="abs story-text">Pellentesque convallis molestie enim sit amet efficitur. Etiam id imperdiet lectus. Vivamus lacus justo, ultrices nec erat in, euismod iaculis mauris. Vivamus eleifend vitae tortor eu malesuada. In ac malesuada lacus, et consectetur ante. Fusce vitae lectus sit amet mi pulvinar maximus. Aenean placerat, nibh vel accumsan aliquet, magna nibh accumsan nibh, ac tempor nunc ipsum ac tellus. Cras augue magna, placerat eget nulla non, congue suscipit neque.</div>
<a class="abs btn btn-navy story-btn">Read More</a>
<div class="abs story-photo" role="img" aria-label="Crowd with raised hands at a worship concert"></div>

<!-- pastor & podcasts -->
<h2 class="abs sec-title" style="left:145px;top:2822px">About Pastor</h2>
<div class="abs pastor-photo" role="img" aria-label="Portrait of the pastor in clerical dress"></div>
<div class="abs pastor-text">Pellentesque convallis molestie enim sit amet efficitur. Etiam id imperdiet lectus. Vivamus lacus justo, ultrices nec erat in, euismod iaculis mauris. Vivamus eleifend vitae tortor eu malesuada. In ac malesuada lacus, et consectetur ante. Fusce vitae lectus sit amet mi pulvinar maximus. Aenean placerat, nibh vel accumsan aliquet, magna nibh accumsan nibh, ac tempor nunc ipsum ac tellus. Cras augue magna, placerat eget nulla non, congue suscipit neque.</div>
<h2 class="abs sec-title" style="left:628px;top:2822px">Podcasts</h2>
<div class="abs pod" style="top:2870px"><span class="play"><svg width="12" height="14" viewBox="0 0 12 14"><path d="M1 1l10 6-10 6z" fill="#fff"/></svg></span><div><h4>Curabitur venenatis lacinia ornare</h4><span>5 April, 2019</span></div></div>
<div class="abs pod" style="top:2940px"><span class="play"><svg width="12" height="14" viewBox="0 0 12 14"><path d="M1 1l10 6-10 6z" fill="#fff"/></svg></span><div><h4>Quisque aliquet ex nec est vestibulum pulvinar</h4><span>5 April, 2019</span></div></div>
<div class="abs pod" style="top:3010px;border-bottom:none"><span class="play"><svg width="12" height="14" viewBox="0 0 12 14"><path d="M1 1l10 6-10 6z" fill="#fff"/></svg></span><div><h4>Pellentesque convallis molestie enim amet efficitur</h4><span>5 April, 2019</span></div></div>

<!-- events -->
<div class="abs events"></div>
<h2 class="abs sec-title events-title">Upcoming Events</h2>
<div class="abs card" style="top:3236px">
  <div class="ph" style="background:linear-gradient(135deg,#3a2a20,#b08a62 50%,#5a3a24)" role="img" aria-label="Empty church pews"></div>
  <div class="body"><h4>Maecenas vel tortor accumsan quam varius imperdiet</h4><div class="when">April 7 - 2019 &nbsp;at &nbsp;10:15 AM</div><p>Phasellus consequat sagittis nisl suscipit feugiat. Cras eget leo sed nunc hendrerit ultricies eu ut nisl. Praesent iaculis faucibus urna sit amet lacinia. Maecenas consequat justo enim, ac mattis massa imperdiet quis. Fusce eget neque elit. Sed augue orci, elementum in magna congue.</p><span class="more">Read More</span></div>
</div>
<div class="abs card" style="top:3444px">
  <div class="ph" style="background:linear-gradient(180deg,#5a7fb0,#e8e8e8 45%,#c0622a 75%,#6a3a1a)" role="img" aria-label="White chapel among autumn trees"></div>
  <div class="body"><h4>Etiam mattis augue vehicula odio posuere sit amet</h4><div class="when">April 7 - 2019 &nbsp;at &nbsp;10:15 AM</div><p>Phasellus consequat sagittis nisl suscipit feugiat. Cras eget leo sed nunc hendrerit ultricies eu ut nisl. Praesent iaculis faucibus urna sit amet lacinia. Maecenas consequat justo enim, ac mattis massa imperdiet quis. Fusce eget neque elit. Sed augue orci, elementum in magna congue.</p><span class="more">Read More</span></div>
</div>
<div class="abs card" style="top:3652px">
  <div class="ph" style="background:linear-gradient(135deg,#f0ece6,#c9b8a6 50%,#3a2a22)" role="img" aria-label="Wedding couple holding hands with flowers"></div>
  <div class="body"><h4>Etiam vel massa elementum, bibendum tellus venenatis</h4><div class="when">April 7 - 2019 &nbsp;at &nbsp;10:15 AM</div><p>Phasellus consequat sagittis nisl suscipit feugiat. Cras eget leo sed nunc hendrerit ultricies eu ut nisl. Praesent iaculis faucibus urna sit amet lacinia. Maecenas consequat justo enim, ac mattis massa imperdiet quis. Fusce eget neque elit. Sed augue orci, elementum in magna congue.</p><span class="more">Read More</span></div>
</div>

<!-- footer -->
<div class="abs footer"></div>
<div class="abs fcol" style="left:145px;top:3970px;width:300px">
  <h4>Latest Sermons</h4>
  <div class="fitem"><span class="th" style="background:linear-gradient(135deg,#7a4a2a,#c8a070)" role="img" aria-label="Sermon thumbnail"></span><p>Etiam mattis augue vehicula odio posuere sit amet tempus lectus. Nulla facilisi. Etiam vel massa.</p></div>
  <div class="fitem"><span class="th" style="background:linear-gradient(135deg,#3a2a20,#a88a70)" role="img" aria-label="Sermon thumbnail"></span><p>Quisque aliquet ex nec est vestibulum pulvinar. Pellentesque convallis molestie enim sit amet efficitur.</p></div>
</div>
<div class="abs fcol" style="left:458px;top:3970px">
  <h4>Sermons Tags</h4>
  <div class="tags"><span>Fusce</span><span>Aenean</span><span>Proin</span><span>Curabitur</span><span>Pellentesque</span><span>Nulla</span><span>Vivamus</span><span>Fusce</span><span>Vestibulum</span></div>
</div>
<div class="abs fcol" style="left:772px;top:3970px;width:290px">
  <h4>Latest News</h4>
  <div class="fitem"><span class="th" style="background:linear-gradient(135deg,#5a3a24,#b08a62)" role="img" aria-label="News thumbnail"></span><p>Etiam mattis augue vehicula odio posuere sit amet tempus lectus. Nulla facilisi. Etiam vel massa.</p></div>
  <div class="fitem"><span class="th" style="background:linear-gradient(135deg,#c8652d,#2a1a20)" role="img" aria-label="News thumbnail"></span><p>Quisque aliquet ex nec est vestibulum pulvinar. Pellentesque convallis molestie enim sit amet efficitur.</p></div>
</div>
<div class="abs flinks"><span>Home</span>|<span>Team</span>|<span>Features</span>|<span>Events</span>|<span>Sermons</span>|<span>Blog</span>|<span>Contacts</span>|<span>Donate</span></div>
<div class="abs copy">Copyright © 2019 · Wellspring Grace Church · All rights reserved.</div>
<div class="abs social"><i></i><i></i><i></i></div>

</body>
</html>
```